Open Harbor book needs a cover design

I need a front and back cover design that demonstrates a strong sense of possibility that trust can be repaired even if things look bleak. Repairing trust is difficult, but this book is full of wisdom, proven strategies, and doctoral research to help people strengthen relationships and improve trust. It can help any group: business, nonprofit, education, service. Showing diversity of groups and people is very important. For the cover title, there should be a play on words: "Open Harbor: Is it? Within Reach" should have the words "is it?" crossed out and the words "It IS! should be replaced there in a striking way. Perhaps in red ink. For publishing purposes, book will be titled Open Harbor: It IS Within Reach! Please see the attachment for an example. The book layout is approximately 260 pages.

A business self-help book, but the target is any person in a group that feels they have lost trust in each other. It can be just a normal person struggling in a volunteer group they are a part of, or a supervisor whose group is not working well together. It can be a leader who just wants their group to be stronger.

Business Management

• Allise - I believe is being used on the interior of the book for the title page and headings

• Show hope and possibility in the midst of difficulty. Must have a play on the words in the title "Open Harbor: Is it? Within Reach" with crossing out "is it?" with "It IS!" (see attached example) Must include the author's name: Marla Quentin, PhD Must include a smaller tagline: "Practical Steps to Move Teams Forward Again"
• Showing diverse people, or hands. Diverse kinds of groups - not just business. A colorful cover. Maybe show the complexity of trust when it is broken...broken pieces of trust that are then picked up and put together when people work together. Could show people (or images of hands) or other ways to show that it's a choice and it is possible to repair broken trust. I'd also like to convey a sense of a group - not just random people. That they have something at stake to work on repairing trust together and this book can help them.
• If images of people are used, just showing one gender or race is not okay. Nor just binary choices: like an image containing one man and one woman, or one white person and one person of color - otherwise it seems that the book on Open Harbor is about race or gender relations.

```html
<!DOCTYPE html>
<html lang="en">
<head>
<meta charset="utf-8">
<title>Open Harbor – Book Cover</title>
<link rel="stylesheet" href="https://fonts.googleapis.com/css2?family=Marcellus+SC&family=Kalam:wght@400;700&family=Andika:wght@700&family=Patrick+Hand&family=Montserrat:wght@400&display=swap">
<style>
  :root {
    --stage: #05101f;
    --cover-deep: #1c3f99;
    --cover-mid: #2a58bd;
    --cover-light: #4c74c9;
    --gold: #c99a3e;
    --gold-light: #e2bd6a;
    --ink-red: #d8251c;
    --white: #ffffff;
    --tag-yellow: #f3e12a;
    --glow: #43b7f2;
  }
  html, body {
    margin: 0;
    width: 1200px;
    height: 1200px;
    overflow: hidden;
    background: var(--stage);
  }
  .canvas {
    width: 1200px;
    height: 1200px;
    display: flex;
    align-items: center;
    justify-content: center;
  }
  .cover {
    width: 760px;
    height: 1140px;
    display: block;
  }
  .title-word {
    font-family: "Marcellus SC", serif;
    fill: url(#goldFill);
  }
  .title-shadow { fill: rgba(0,0,0,0.35); font-family: "Marcellus SC", serif; }
  .affirm { font-family: "Kalam", cursive; font-weight: 700; fill: var(--white); font-style: italic; }
  .doubt { font-family: "Kalam", cursive; font-weight: 400; fill: var(--ink-red); }
  .strike { stroke: var(--ink-red); stroke-width: 4; stroke-linecap: round; fill: none; }
  .promise { font-family: "Andika", sans-serif; font-weight: 700; fill: var(--white); }
  .tagline { font-family: "Patrick Hand", cursive; fill: var(--tag-yellow); }
  .author { font-family: "Patrick Hand", cursive; fill: var(--gold-light); }
  .frame { stroke: var(--gold); stroke-width: 6; fill: none; }
  .publisher { font-family: "Montserrat", sans-serif; fill: var(--white); letter-spacing: 1px; }
</style>
</head>
<body>
<main class="canvas">
  <svg class="cover" viewBox="0 0 760 1140" xmlns="http://www.w3.org/2000/svg">
    <defs>
      <linearGradient id="coverFill" x1="0" y1="0" x2="1" y2="1">
        <stop offset="0" stop-color="#4c74c9"/>
        <stop offset="0.45" stop-color="#2a58bd"/>
        <stop offset="1" stop-color="#1c3f99"/>
      </linearGradient>
      <linearGradient id="goldFill" x1="0" y1="0" x2="0" y2="1">
        <stop offset="0" stop-color="#e6c274"/>
        <stop offset="0.5" stop-color="#c4923a"/>
        <stop offset="1" stop-color="#9c6d24"/>
      </linearGradient>
      <radialGradient id="handsGlow" cx="0.5" cy="0.55" r="0.6">
        <stop offset="0" stop-color="#7fd3fb"/>
        <stop offset="0.45" stop-color="#43b7f2"/>
        <stop offset="1" stop-color="#2a58bd" stop-opacity="0"/>
      </radialGradient>
      <linearGradient id="handsTone" x1="0" y1="0" x2="0" y2="1">
        <stop offset="0" stop-color="#b88a68"/>
        <stop offset="1" stop-color="#6e4a33"/>
      </linearGradient>
    </defs>

    <rect class="cover-ground" width="760" height="1140" fill="url(#coverFill)"/>

    <g class="hands-photo" role="img" aria-label="Photo of several raised hands of different skin tones meeting together in a bright blue glow">
      <ellipse cx="390" cy="1000" rx="300" ry="200" fill="url(#handsGlow)"/>
      <path d="M240 1140 L300 920 Q390 860 480 920 L540 1140 Z" fill="url(#handsTone)" opacity="0.85"/>
    </g>

    <g class="frame-lines">
      <line class="frame" x1="137" y1="0" x2="137" y2="795"/>
      <line class="frame" x1="644" y1="0" x2="644" y2="795"/>
      <line class="frame" x1="134" y1="792" x2="200" y2="792"/>
      <line class="frame" x1="582" y1="792" x2="647" y2="792"/>
    </g>

    <g class="title">
      <text class="title-shadow" x="394" y="264" text-anchor="middle" font-size="190" textLength="360" lengthAdjust="spacingAndGlyphs">OPEN</text>
      <text class="title-word" x="390" y="260" text-anchor="middle" font-size="190" textLength="360" lengthAdjust="spacingAndGlyphs">OPEN</text>
      <text class="title-shadow" x="394" y="416" text-anchor="middle" font-size="175" textLength="420" lengthAdjust="spacingAndGlyphs">HARBOR</text>
      <text class="title-word" x="390" y="412" text-anchor="middle" font-size="175" textLength="420" lengthAdjust="spacingAndGlyphs">HARBOR</text>
    </g>

    <g class="wordplay">
      <text class="affirm" x="385" y="484" text-anchor="middle" font-size="58">It Is</text>
      <text class="doubt" x="382" y="530" text-anchor="middle" font-size="44">Is it?</text>
      <path class="strike" d="M340 508 L424 526 M340 526 L426 500"/>
    </g>

    <text class="promise" x="390" y="630" text-anchor="middle" font-size="92" textLength="470" lengthAdjust="spacingAndGlyphs">Within Reach</text>

    <g class="tagline-block">
      <text class="tagline" x="390" y="676" text-anchor="middle" font-size="36">Practical Steps to Move</text>
      <text class="tagline" x="390" y="714" text-anchor="middle" font-size="36">Teams Forward Again</text>
    </g>

    <text class="author" x="391" y="806" text-anchor="middle" font-size="44">Marla Quentin, PhD</text>

    <g class="publisher-mark">
      <rect x="588" y="1052" width="22" height="22" fill="var(--white)"/>
      <text class="publisher" x="618" y="1062" font-size="14">NORTHGATE</text>
      <text class="publisher" x="618" y="1078" font-size="14">PRESS</text>
    </g>
  </svg>
</main>
</body>
</html>
```